New B2C website design to help dads be better dads

DadHarbor is a website to help dads be the “best dad you can be.”

We require our website to be designed into a PSD format, no coding necessary.

The general concept is a two-page design. The first page is the login page, the second page is the home page. Once at the home page, rather than navigating to and from different pages, the user will push and pull through different visual and functional layers of the hierarchy. In theory, this should add to the user experience by having a visual anchor of where they are (through layered pagination) as well as improving loading times since the new information should only be a delta in data load versus a brand new page load.

The general look-and-feel we are going for is clean, simple, minimal. This means that the winning design will show us a good eye for web-optimized typography, good use of white (negative) space, and good use of a visually pleasing grid.

We require a total of 6 page "views" plus the landing page. We note that many of the views are similar to one another.
Landing page
Milestone view
Task view
Content view, articles
Content view, products
Search view
What's new view

Please review all of the additional information provided as well as the attachments for examples.

We provide the following websites as good references for:

Typography:
http://example-kelvorn.com/journal/

Use of white space:
http://www.trenvaskit.com/
http://moldrefin.com/

Example for “scrolling” page concept as well as good balance of color, typography, and white space:
http://www.qorbitalmeet.eu/

Please contact us with questions so that we can guide your design effort.
Updates

Hello designers,

The following information is added to help guide the design process:

1.  For the text dialogue below the landing page, please assume the following word count:
"why are we making dad harbor?": 250 words
"who are we?" 200 words
"what's the deal with the penguin logo?" 300 words

For the social media links, please see http://www.gravelplumbs.com/
Notice the floating "social" bar that is always to the right.  This is the concept we are going for, please try to implement this as you see fit. 

Target Market(s)

Fathers of young children ages 0-6 years old.

Industry/Entity Type

Product

Font styles to use
Sans Serif

Requirements
Must have
• Clean lines, minimal design concept

Incorporation of our logo (see attached document)

Header content is static for all views after landing page, see example

This page WILL be responsive, please keep that in mind when designing
The timeline bar should be to the left, with the timeline bar’s “milestones” also being responsive.

Designer is free to suggest font types, but any fonts used must be royalty-free and web-optimized. We request a minimum number of font types as well as fonts that load relatively fast. We reinforce that visually appealing typography is a significant factor in the winning design choice.

While we are not expecting the winning design to include code, please keep in mind that the final implementation needs to be optimized for desktop, tablet, and mobile platforms.

If you are using stock photography that is not generated by you, please provide where/how we can obtain imagery, as well as price.

All custom graphics must be available in original formats; Photoshop/GIMP layered files for layout design, and vector formats for logos, icons and other graphical elements.

Please incorporate “Blue” into design elements as you see fit, as the RGB 67 74 169 Blue is the primary color used in our brand. The complement to this blue is 255 202 0, a brownish orange. Feel free to use this color as well, although please keep it to a lesser amount.

Background color is your choice, do not feel the need to use the grey.
Should not have
• Excessive graphical content such that it affects loading times

Excessive use of too many font types such that it affects loading times

```html
<!DOCTYPE html>
<html lang="en">
<head>
<meta charset="utf-8">
<title>DadHarbor — Be the best dad you can be</title>
<link href="https://fonts.googleapis.com/css2?family=Source+Sans+3:wght@400;600&family=Arvo:wght@400;700&family=Fredoka:wght@600&display=swap" rel="stylesheet">
<style>
  :root {
    --brand-blue: #434aa9;
    --brand-yellow: #f5c518;
    --accent-yellow: #e8b10c;
    --text-body: #6b6b6b;
    --text-dark: #2a2a2a;
    --line: #e2e2e2;
    --footer-bg: #f3f3f3;
    --white: #ffffff;
    --sky-light: #e9eef2;
    --sky-mid: #c9d3dc;
    --shirt: #b8bde0;
    --skin: #c89a7a;
  }
  * { box-sizing: border-box; margin: 0; padding: 0; }
  html, body { width: 836px; height: 1200px; overflow: hidden; background: var(--white); }
  body { position: relative; font-family: "Source Sans 3", Arial, sans-serif; color: var(--text-body); }

  /* Header */
  .site-header { position: absolute; left: 0; top: 0; width: 836px; height: 130px; background: var(--white); }
  .brand { position: absolute; left: 70px; top: 78px; display: flex; align-items: center; gap: 8px; }
  .brand-dot { width: 14px; height: 14px; border-radius: 50%; background: var(--brand-blue); }
  .brand-name { font-family: "Source Sans 3", Arial, sans-serif; font-weight: 600; font-size: 22px; color: var(--brand-blue); }
  .login { position: absolute; top: 43px; left: 490px; display: flex; gap: 5px; }
  .login-field { width: 104px; height: 25px; border: 1px solid #d6d6d6; border-radius: 2px; font-size: 10.5px; color: #9a9a9a; padding: 5px 10px; background: var(--white); }
  .login-button { width: 53px; height: 25px; background: var(--brand-yellow); border: 1px solid var(--accent-yellow); border-radius: 2px; font-size: 11px; color: #7a5a00; text-align: center; line-height: 23px; margin-left: 0; }
  .login-links { position: absolute; top: 76px; right: 75px; font-size: 10.5px; color: #7a7a7a; display: flex; gap: 14px; }

  /* Hero */
  .hero { position: absolute; left: 0; top: 130px; width: 836px; height: 428px; }
  .hero-photo { position: absolute; inset: 0;
    background: radial-gradient(ellipse at 48% 35%, var(--skin) 0%, rgba(200,154,122,0.55) 18%, rgba(200,154,122,0) 40%),
                radial-gradient(ellipse at 55% 95%, var(--shirt) 0%, rgba(184,189,224,0) 55%),
                linear-gradient(180deg, var(--sky-light) 0%, var(--sky-mid) 55%, #d9d4d2 100%); }
  .hero-title { position: absolute; left: 203px; top: 218px; width: 429px; height: 42px; background: var(--brand-yellow); font-family: "Fredoka", Arial, sans-serif; font-weight: 600; font-size: 25px; letter-spacing: 1px; color: var(--text-dark); text-align: center; line-height: 42px; }
  .hero-subtitle { position: absolute; left: 166px; top: 265px; width: 502px; height: 33px; background: var(--brand-yellow); font-family: "Arvo", Georgia, serif; font-size: 18.5px; color: #3a3a3a; text-align: center; line-height: 33px; }
  .hero-intro { position: absolute; left: 89px; top: 311px; width: 659px; height: 68px; background: rgba(255,255,255,0.88); font-size: 11px; line-height: 17.5px; color: var(--text-dark); text-align: center; padding: 8px 12px; }
  .hero-cta { position: absolute; left: 312px; top: 384px; width: 211px; height: 24px; background: rgba(255,255,255,0.92); font-family: "Arvo", Georgia, serif; font-size: 10.5px; color: var(--brand-blue); text-align: center; line-height: 24px; }
  .hero-cta::after { content: ""; position: absolute; left: 98px; top: 24px; border: 7px solid transparent; border-top-color: rgba(255,255,255,0.92); border-bottom: 0; }

  /* About */
  .about-title { position: absolute; top: 583px; left: 0; width: 836px; text-align: center; font-family: "Arvo", Georgia, serif; font-size: 22px; color: var(--accent-yellow); letter-spacing: 0.5px; }
  .about-item { position: absolute; left: 93px; width: 660px; }
  .about-photo { position: absolute; width: 106px; height: 106px; border-radius: 50%; box-shadow: 0 2px 3px rgba(0,0,0,0.25); }
  .photo-sky { background: linear-gradient(180deg, #5f8a9c 0%, #a9c5cf 60%, #e6e9ea 100%); }
  .photo-seat { background: radial-gradient(circle at 55% 50%, #8d96a8 0%, #4f5868 60%, #2e3440 100%); }
  .photo-sleep { background: radial-gradient(circle at 45% 60%, #d9d2cb 0%, #7d7570 50%, #1e1c1b 100%); }
  .about-heading { font-family: "Arvo", Georgia, serif; font-weight: 400; font-size: 19px; color: var(--brand-blue); margin-bottom: 8px; }
  .about-text { font-size: 11.5px; line-height: 17.5px; color: var(--text-body); text-align: justify; }
  .divider { position: absolute; left: 93px; width: 660px; height: 1px; background: linear-gradient(90deg, rgba(226,226,226,0), var(--line) 15%, var(--line) 85%, rgba(226,226,226,0)); }

  /* Footer */
  .site-footer { position: absolute; left: 0; top: 1115px; width: 836px; height: 85px; background: var(--footer-bg); border-top: 1px solid #dadada; }
  .footer-nav { position: absolute; left: 70px; top: 22px; font-size: 10.5px; color: #555; display: flex; gap: 7px; }
  .footer-nav .sep { color: #aaa; }
  .copyright { position: absolute; left: 70px; top: 47px; font-size: 10.5px; color: #666; word-spacing: 2px; }
  .social { position: absolute; left: 682px; top: 32px; display: flex; gap: 9px; }
  .social-dot { width: 22px; height: 22px; border-radius: 50%; }
  .social-dot.one { background: #3b5495; }
  .social-dot.two { background: #39b3e6; }
  .social-dot.top { background: #6d6d6d; }
</style>
</head>
<body>
  <header class="site-header">
    <div class="brand"><span class="brand-dot"></span><span class="brand-name">DadHarbor</span></div>
    <div class="login">
      <div class="login-field">Username</div>
      <div class="login-field">********</div>
      <div class="login-button">SIGN IN</div>
    </div>
    <div class="login-links"><span>Forgot login?</span><span>Request access</span></div>
  </header>

  <section class="hero">
    <div class="hero-photo" role="img" aria-label="Photo of a father being kissed on the cheek by his young daughter by the sea"></div>
    <h1 class="hero-title">BE THE BEST DAD YOU CAN BE</h1>
    <p class="hero-subtitle">The portal created exclusively for dads, by dads</p>
    <p class="hero-intro">Aliquam quis dui a diam sagittis suscipit. Sed suscipit porta interdum. Class aptent taciti sociosqu ad litora torquent per conubia nostra, per inceptos himenaeos. Nullam felis leo, iaculis id odio at, pretium mollis dui. Pellentesque viverra dapibus diam, id bibendum magna accum san eu. Fusce interdum condimentum sapien eu vestibulum. Ut tempor libero eu purus euismod sodales.</p>
    <div class="hero-cta">LEARN MORE ABOUT DADHARBOR</div>
  </section>

  <h2 class="about-title">ABOUT DAD HARBOR</h2>

  <article class="about-item" style="top:636px;">
    <div class="about-photo photo-sky" style="left:0;top:0;" role="img" aria-label="Photo of a father lifting his child into the sky"></div>
    <div style="margin-left:127px;">
      <h3 class="about-heading">Why are we making Dad Harbor?</h3>
      <p class="about-text">Aliquam quis dui a diam sagittis suscipit. Sed suscipit porta interdum. Class aptent taciti sociosqu ad litora torquent per conubia nostra, per inceptos himenaeos. Nullam felis leo, iaculis id odio at, pretium mollis dui. Pellentesque viverra dapibus diam, id bibendum magna accum san eu. Fusce interdum condimentum sapien eu vestibulum. Ut tempor libero eu purus euismod sodales.</p>
    </div>
  </article>
  <div class="divider" style="top:772px;"></div>

  <article class="about-item" style="top:798px;">
    <div style="width:532px;">
      <h3 class="about-heading">Who are we?</h3>
      <p class="about-text">Aliquam quis dui a diam sagittis suscipit. Sed suscipit porta interdum. Class aptent taciti sociosqu ad litora torquent per conubia nostra, per inceptos himenaeos. Nullam felis leo, iaculis id odio at, pretium mollis dui. Pellentesque viverra dapibus diam, id bibendum magna accum san eu. Fusce interdum condimentum sapien eu vestibulum. Ut tempor libero eu purus euismod sodales.</p>
    </div>
    <div class="about-photo photo-seat" style="left:552px;top:5px;" role="img" aria-label="Photo of a baby sitting in a car seat"></div>
  </article>
  <div class="divider" style="top:939px;"></div>

  <article class="about-item" style="top:969px;">
    <div class="about-photo photo-sleep" style="left:0;top:1px;" role="img" aria-label="Black and white photo of a sleeping baby held close"></div>
    <div style="margin-left:127px;">
      <h3 class="about-heading">Why are we making Dad Harbor?</h3>
      <p class="about-text">Aliquam quis dui a diam sagittis suscipit. Sed suscipit porta interdum. Class aptent taciti sociosqu ad litora torquent per conubia nostra, per inceptos himenaeos. Nullam felis leo, iaculis id odio at, pretium mollis dui. Pellentesque viverra dapibus diam, id bibendum magna accum san eu. Fusce interdum condimentum sapien eu vestibulum. Ut tempor libero eu purus euismod sodales.</p>
    </div>
  </article>

  <footer class="site-footer">
    <nav class="footer-nav">
      <span>Home</span><span class="sep">/</span><span>About us</span><span class="sep">/</span><span>Products</span><span class="sep">/</span><span>Articles</span><span class="sep">/</span><span>Contact us</span>
    </nav>
    <p class="copyright">Copyright © 2013 Dad Harbor. All rights reserved.</p>
    <div class="social">
      <span class="social-dot one"></span>
      <span class="social-dot two"></span>
      <svg class="social-dot top" width="22" height="22" viewBox="0 0 22 22" aria-label="Back to top">
        <circle cx="11" cy="11" r="11" fill="#6d6d6d"/>
        <path d="M6 13 L11 8 L16 13" fill="none" stroke="#ffffff" stroke-width="3" stroke-linecap="round" stroke-linejoin="round"/>
      </svg>
    </div>
  </footer>
</body>
</html>
```